Stationery Design Task - Stationary, memo and report templates for professional services company

Looking for someone to update stationary design but just as importantly come up with a template for reports and memos for use in our consulting firm. Would also like some brand use guidelines to be able to share with our whole team. We have an existing logo that we like. Need to update with a more contemporary look so that our deliverables to clients look good and professional yet stylish. This is for business to business communications. No need for envelope design. Important to have design for multiple pages, i.e. first page of a report and then 2nd page. Need to use in MS word documents so must be easy to use and replicate. Don't want something overly complex. Clean, fresh looking is best.

Industry/Entity Type

Information Technology

Font styles to use
Sans Serif

Colors
33a6d7
0792cd
85cae6
cee9f5
cedeed
85abd2
3377b5
0455a3

Requirements
Must have
• Clean look but with a little style or pop. Something that can easily be used in word documents. Need to have page styles that have a first page of a report (not a cover page) and then secondary page.
Nice to have
• - Although the dark blue is our primary color. Might be willing to look at some accent color as well.
Should not have
• Not just our logo on the page with a color bar.

```html
<!DOCTYPE html>
<html lang="en">
<head>
<meta charset="utf-8">
<title>Northvale Systems – Stationery Set</title>
<link href="https://fonts.googleapis.com/css2?family=Roboto:wght@300;400;500;700;900&family=Montserrat:wght@300;400&display=swap" rel="stylesheet">
<style>
  :root {
    --stage: #666666;
    --brand: #0792cd;
    --brand-deep: #0455a3;
    --brand-mid: #3377b5;
    --brand-light: #33a6d7;
    --ink: #3c3c3c;
    --ink-soft: #555555;
    --rule: #8a8a8a;
    --page-top: #ffffff;
    --page-bottom: #cdcdcd;
  }
  * { box-sizing: border-box; margin: 0; padding: 0; }
  html, body { width: 932px; height: 1200px; overflow: hidden; }
  body { background: var(--stage); position: relative; font-family: 'Roboto', sans-serif; }

  .page {
    position: absolute; width: 381px; height: 537px; overflow: hidden;
    background: linear-gradient(180deg, var(--page-top) 0%, var(--page-bottom) 100%);
    box-shadow: 0 1px 3px rgba(0,0,0,.25);
  }
  .page--cover { left: 61px; top: 50px; }
  .page--contents { left: 485px; top: 50px; }
  .page--letter { left: 64px; top: 620px; }
  .page--continuation { left: 483px; top: 620px;
    background: linear-gradient(90deg, #d4d4d4 0%, #f4f4f4 100%); }

  .brand-name {
    position: absolute; display: flex; align-items: center; gap: 7px;
    font-family: 'Roboto', sans-serif; font-weight: 700; color: var(--brand);
    letter-spacing: .3px; white-space: nowrap;
  }
  .brand-name__dot { width: 12px; height: 12px; border-radius: 50%; background: var(--brand); flex: none; }

  /* Cover */
  .cover__pattern {
    position: absolute; left: 0; top: 22px; width: 115px; height: 490px;
    background: linear-gradient(180deg, #2a8fd0 0%, #0a7cc8 55%, #0d74bd 100%);
    clip-path: polygon(0 0, 30% 4%, 40% 12%, 75% 14%, 85% 22%, 100% 30%, 92% 40%, 100% 50%,
      90% 60%, 100% 72%, 88% 82%, 60% 90%, 35% 96%, 0 100%);
  }
  .cover__brand { left: 116px; top: 66px; font-size: 17px; }
  .cover__title {
    position: absolute; left: 120px; width: 260px; top: 202px; text-align: center;
    font-weight: 900; font-size: 52px; line-height: 44px; color: var(--brand-mid);
  }
  .cover__subtitle {
    position: absolute; left: 166px; width: 157px; top: 362px; text-align: center;
    font-weight: 700; font-size: 16px; color: #6a6a6a; padding: 4px 0 3px;
    border-top: 1px solid var(--rule); border-bottom: 1px solid var(--rule);
  }
  .cover__date {
    position: absolute; left: 120px; width: 260px; top: 455px; text-align: center;
    font-weight: 500; font-size: 14px; color: var(--brand);
  }

  /* Contents */
  .contents__title {
    position: absolute; left: 31px; top: 41px; width: 318px;
    font-size: 16px; font-weight: 400; color: var(--brand); padding-bottom: 6px;
    border-bottom: 1px solid #777;
  }
  .contents__list { position: absolute; left: 29px; top: 77px; width: 314px; list-style: none; }
  .contents__item {
    display: flex; align-items: baseline; height: 16.2px;
    font-size: 9.6px; font-weight: 300; color: var(--ink);
  }
  .contents__item--section { color: var(--brand); font-weight: 500; }
  .contents__leader { flex: 1; border-bottom: 1px dotted #9a9a9a; margin: 0 4px; transform: translateY(-2px); }
  .contents__page { color: var(--ink); font-weight: 300; min-width: 10px; text-align: right; }

  .band {
    position: absolute; left: 0; width: 100%;
    background: linear-gradient(180deg, var(--brand-light) 0%, var(--brand) 100%);
    clip-path: polygon(0 45%, 6% 25%, 12% 45%, 18% 10%, 25% 30%, 32% 15%, 38% 40%, 45% 20%,
      52% 45%, 58% 15%, 64% 30%, 70% 0, 77% 25%, 83% 10%, 90% 35%, 96% 20%, 100% 5%, 100% 100%, 0 100%);
  }
  .page--contents .band { top: 497px; height: 40px; }

  /* Letter */
  .letter__brand { left: 104px; top: 46px; font-size: 16px; }
  .letter__body { position: absolute; left: 34px; top: 150px; width: 318px; font-family: 'Montserrat', sans-serif; color: var(--ink-soft); }
  .letter__salutation { font-size: 10px; font-weight: 400; margin-bottom: 14px; }
  .letter__para { font-size: 5.4px; line-height: 8.2px; font-weight: 400; margin-bottom: 8px; text-align: justify; }
  .letter__closing { font-size: 5.4px; margin-top: 16px; }
  .letter__signature {
    margin-top: 12px; width: 70px; height: 28px;
    background: linear-gradient(90deg, rgba(51,119,181,.35), rgba(51,119,181,.08));
    border-radius: 4px;
  }
  .page--letter .band { top: 466px; height: 71px; clip-path: polygon(0 25%, 6% 12%, 12% 28%, 18% 5%, 25% 20%, 32% 8%, 38% 25%, 45% 10%, 52% 28%, 58% 8%, 64% 20%, 70% 0, 77% 15%, 83% 5%, 90% 22%, 96% 10%, 100% 3%, 100% 100%, 0 100%); }
  .letter__contact {
    position: absolute; left: 0; top: 497px; width: 100%; height: 16px;
    background: var(--brand-deep); opacity: .85;
    display: flex; align-items: center; justify-content: center; gap: 12px;
    color: #fff; font-size: 6.6px; font-weight: 500; letter-spacing: .1px;
  }

  /* Continuation */
  .continuation__brand { right: 28px; bottom: 28px; font-size: 9px; gap: 5px; }
  .continuation__brand .brand-name__dot { width: 10px; height: 10px; }
</style>
</head>
<body>

<section class="page page--cover">
  <div class="cover__pattern" role="img" aria-label="Blue hexagon pattern along the left edge"></div>
  <div class="brand-name cover__brand"><span class="brand-name__dot"></span>NORTHVALE SYSTEMS</div>
  <h1 class="cover__title">IRON<br>RIDGE</h1>
  <p class="cover__subtitle">IT SUPPORT GUIDE</p>
  <p class="cover__date">SEBTEMBER 2018</p>
</section>

<section class="page page--contents">
  <h2 class="contents__title">Table of content</h2>
  <ol class="contents__list">
    <li class="contents__item contents__item--section"><span>What's New</span><span class="contents__leader"></span><span class="contents__page">2</span></li>
    <li class="contents__item"><span>Proin pede metus, vulputate nec, fermentum fringil</span><span class="contents__leader"></span><span class="contents__page">2</span></li>
    <li class="contents__item contents__item--section"><span>Vehicula</span><span class="contents__leader"></span><span class="contents__page">5</span></li>
    <li class="contents__item"><span>Vitae, justo.d</span><span class="contents__leader"></span><span class="contents__page">5</span></li>
    <li class="contents__item"><span>Etiam neque. Fusce</span><span class="contents__leader"></span><span class="contents__page">5</span></li>
    <li class="contents__item contents__item--section"><span>Tellus odio, d</span><span class="contents__leader"></span><span class="contents__page">8</span></li>
    <li class="contents__item"><span>apibus id ferment</span><span class="contents__leader"></span><span class="contents__page">8</span></li>
    <li class="contents__item contents__item--section"><span>Um quis, suscipit id ers</span><span class="contents__leader"></span><span class="contents__page">10</span></li>
    <li class="contents__item"><span>Duis pulvinar. Etiam</span><span class="contents__leader"></span><span class="contents__page">10</span></li>
    <li class="contents__item"><span>egestas wisi a erat. Vi</span><span class="contents__leader"></span><span class="contents__page">10</span></li>
    <li class="contents__item contents__item--section"><span>Vamus luctus egestas</span><span class="contents__leader"></span><span class="contents__page">15</span></li>
    <li class="contents__item"><span>leo. Aenean vel massa</span><span class="contents__leader"></span><span class="contents__page">15</span></li>
    <li class="contents__item contents__item--section"><span>Quis mauris vehicula</span><span class="contents__leader"></span><span class="contents__page">17</span></li>
    <li class="contents__item"><span>lacinia. Nullam at arcu</span><span class="contents__leader"></span><span class="contents__page">18</span></li>
    <li class="contents__item contents__item--section"><span>a est sollicitudin euism</span><span class="contents__leader"></span><span class="contents__page">18</span></li>
    <li class="contents__item"><span>od. Et harum quidem r</span><span class="contents__leader"></span><span class="contents__page">22</span></li>
    <li class="contents__item"><span>erum facilis est et exp</span><span class="contents__leader"></span><span class="contents__page">22</span></li>
    <li class="contents__item"><span>edita distinctio. Nulla</span><span class="contents__leader"></span><span class="contents__page">22</span></li>
    <li class="contents__item contents__item--section"><span>turpis magna, cursus s</span><span class="contents__leader"></span><span class="contents__page">23</span></li>
    <li class="contents__item"><span>it amet, suscipit a, int</span><span class="contents__leader"></span><span class="contents__page">23</span></li>
    <li class="contents__item"><span>erdum id, felis. Sed ac</span><span class="contents__leader"></span><span class="contents__page">25</span></li>
    <li class="contents__item"><span>dolor sit amet purus m</span><span class="contents__leader"></span><span class="contents__page">25</span></li>
    <li class="contents__item contents__item--section"><span>alesuada congue.Cur</span><span class="contents__leader"></span><span class="contents__page">27</span></li>
    <li class="contents__item"><span>abitur sagittis hendreri</span><span class="contents__leader"></span><span class="contents__page">27</span></li>
    <li class="contents__item"><span>t ante. In rutrum. Nulla</span><span class="contents__leader"></span><span class="contents__page">27</span></li>
  </ol>
  <div class="band" role="img" aria-label="Blue hexagon pattern band along the bottom edge"></div>
</section>

<section class="page page--letter">
  <div class="brand-name letter__brand"><span class="brand-name__dot"></span>NORTHVALE SYSTEMS</div>
  <div class="letter__body">
    <p class="letter__salutation">Dear Mr. Carter,</p>
    <p class="letter__para">Thank you for meeting with our team last week to review your current network setup. Following our visit, we have prepared a short summary of the findings along with the next steps we recommend for your offices. Each item is ranked by urgency and estimated effort so your staff can plan the work.</p>
    <p class="letter__para">Most workstations are in good order, but several servers run software that is no longer supported. We suggest moving these services to managed hosting within the next quarter, which will lower risk and reduce the time your team spends on routine upkeep.</p>
    <p class="letter__para">Backups are running nightly, yet restore tests have not been logged this year. We can schedule a full restore drill with your office manager and document the results. Wireless coverage on the second floor is also weak, and two extra access points would resolve the gaps reported by staff near the meeting rooms.</p>
    <p class="letter__para">Please review the attached guide at your convenience. Our support desk is available on weekdays, and we are happy to walk through any part of this plan in person.</p>
    <p class="letter__closing">Sincerely,</p>
    <div class="letter__signature" role="img" aria-label="Handwritten signature of James Carter"></div>
  </div>
  <div class="band" role="img" aria-label="Blue hexagon pattern band along the bottom edge"></div>
  <div class="letter__contact">
    <span>214 HARBOR STREET, FAIRVIEW, OREGON 97024</span>
    <span>555 014 2290 | HELLO@NORTHVALESYSTEMS.COM</span>
  </div>
</section>

<section class="page page--continuation">
  <div class="brand-name continuation__brand"><span class="brand-name__dot"></span>NORTHVALE SYSTEMS</div>
</section>

</body>
</html>
```